Redesign for a start up airline technology. The website is quelbrion.com.

I need a PowerPoint template that complements our website. I can provide our current template as a starting point.

```html
<!DOCTYPE html>
<html lang="en">
<head>
<meta charset="utf-8">
<title>Quelbrion Presentation Template</title>
<link href="https://fonts.googleapis.com/css2?family=Russo+One&family=Open+Sans:wght@400;600;700&family=Roboto:wght@400;700&display=swap" rel="stylesheet">
<style>
:root{
  --page:#e8e7e8;
  --blue:#0a63b8;
  --blue-deep:#0a55a6;
  --sky:#12a3e3;
  --green:#8fd62a;
  --green-deep:#3f9a2a;
  --ink:#1b1b1b;
  --muted:#6a6a6a;
  --dark:#14110f;
}
*{margin:0;padding:0;box-sizing:border-box}
html,body{width:1046px;height:1200px;overflow:hidden;background:var(--page);font-family:"Open Sans",sans-serif;color:var(--ink)}
.sheet{position:relative;width:1046px;height:1200px}
.slide{position:absolute;width:460px;height:259px;background:#fff;overflow:hidden;box-shadow:0 1px 3px rgba(0,0,0,.08)}
.col-l{left:31px}.col-r{left:555px}
.row1{top:34px}.row2{top:325px}.row3{top:616px}.row4{top:908px}
.abs{position:absolute}
.brand{font-family:"Russo One",sans-serif;color:var(--blue);letter-spacing:.3px}
.brand-top{right:14px;top:20px;font-size:12px}
.band{position:absolute;left:0;top:13px;width:327px;height:31px;border-radius:0 16px 16px 0;background:linear-gradient(90deg,#0a4fa0,#1aa3e6)}
.band h2{font-family:"Russo One",sans-serif;color:#fff;font-weight:400;font-size:16px;line-height:31px;padding-left:34px}
.foot-green{left:0;top:238px;width:212px;height:1px;background:var(--green-deep)}
.foot-blue{left:232px;top:227px;width:228px;height:1px;background:var(--sky)}
.foot-brand{left:210px;top:228px;font-size:8px}
.page-no{left:36px;top:243px;font-size:6.5px;color:#444}
.copy{right:22px;top:236px;font-size:6.5px;color:#444}
.body{font-size:6.2px;line-height:14px;color:#555;text-align:justify}
/* cover */
.cover{background:linear-gradient(100deg,#1a1210 0%,#2a1c16 45%,#1d1b1f 100%)}
.cover-photo{left:190px;top:0;width:270px;height:259px;background:radial-gradient(circle at 60% 45%,#4d6b78 0%,#2b3a40 35%,#2a1d17 70%,transparent 100%)}
.cover .logo{left:36px;top:44px;font-size:26px;color:#fff}
.welcome{left:36px;top:130px;font-family:"Russo One",sans-serif;color:#fff;font-size:12px}
.hero{left:36px;top:150px;font-family:"Russo One",sans-serif;color:var(--sky);font-size:27px}
.tagline{left:36px;top:183px;color:#fff;font-size:7.5px;line-height:15px;width:200px}
.site-btn{left:36px;top:220px;width:78px;height:12px;border-radius:6px;background:var(--green);font-size:4.5px;font-weight:700;color:#15320a;text-align:center;line-height:12px}
/* serve cards */
.card{left:238px;width:190px;height:44px;border-radius:22px;background:#fff;box-shadow:0 1px 6px rgba(0,0,0,.1)}
.ico{position:absolute;width:35px;height:35px;border-radius:50%;background:linear-gradient(160deg,var(--sky),var(--green));display:flex;align-items:center;justify-content:center}
.card .ico{left:3px;top:4.5px}
.card h4{position:absolute;left:44px;top:9px;font-family:"Roboto",sans-serif;font-size:6.5px;color:var(--blue-deep)}
.card p{position:absolute;left:44px;top:20px;width:136px;font-size:3.8px;line-height:8px;color:#666}
/* toc */
.toc-title{left:36px;top:61px;font-family:"Russo One",sans-serif;font-size:16px;color:#111}
.toc-sub{left:36px;top:85px;font-family:"Russo One",sans-serif;font-size:16px;color:var(--sky)}
.toc-intro{left:36px;top:114px;width:150px;font-size:5.6px;line-height:13px;color:#555}
.toc-list{left:242px;top:58px;width:178px;list-style:none}
.toc-list li{height:25px;border-bottom:1px solid #e2e2e2;font-size:6px;line-height:15px;color:#444}
.toc-list li:last-child{border-bottom:1px solid #e2e2e2}
.toc-list b{display:inline-block;width:12px;color:var(--sky);font-weight:400}
/* quote */
.quote{background:var(--blue-deep);text-align:center;color:#fff}
.quote-mark{left:208px;top:38px;width:44px;height:44px;border-radius:50%;background:var(--green)}
.quote h3{left:30px;top:94px;width:400px;font-family:"Russo One",sans-serif;font-weight:400;font-size:15.5px;line-height:26px}
.quote p{left:50px;top:177px;width:360px;font-size:6.5px;line-height:15.7px}
/* about */
.about-photo{left:244px;top:69px;width:193px;height:138px;border-radius:7px;background:linear-gradient(180deg,#d6c7cf 0%,#b49aa6 45%,#6d6a78 80%,#3a3a44 100%)}
/* steps */
.chev{top:69px;width:96px;height:33px}
.chev .ico2{position:absolute;left:15px;top:5px}
.step{top:118px;width:92px}
.step h5{font-family:"Roboto",sans-serif;font-size:6.6px;font-weight:700;margin-bottom:5px}
.step p{font-size:6px;line-height:12.8px;color:#666}
/* leadership */
.leader{top:69px;width:120px;text-align:center}
.ring{margin:0 auto;width:104px;height:104px;border-radius:50%;background:var(--green-deep);padding:11px;position:relative}
.portrait{width:82px;height:82px;border-radius:50%;background:linear-gradient(180deg,#c9d6e2,#8aa0b4 55%,#2b3444)}
.badge{position:absolute;left:42px;bottom:-9px;width:20px;height:20px;border-radius:50%;background:var(--sky);border:2px solid #fff}
.leader h4{margin-top:15px;font-family:"Roboto",sans-serif;font-size:7.6px;color:var(--blue-deep)}
.leader p{margin-top:5px;font-size:5.2px;color:#555}
/* thanks */
.thanks{background:var(--dark)}
.hex{left:206px;top:0;width:254px;height:259px;clip-path:polygon(0 42%,20% 0,100% 0,100% 71%,55% 93%,32% 93%);background:radial-gradient(circle at 60% 45%,#d3dde6 0%,#7c95ad 35%,#2d5d93 70%,#1d3c6b 100%)}
.thanks h2{left:36px;top:39px;font-family:"Russo One",sans-serif;font-weight:400;font-size:18px;color:var(--green)}
.contact{left:36px;width:170px;height:24px}
.contact .ico{left:0;top:0;width:24px;height:24px}
.contact small{position:absolute;left:33px;top:0;font-size:5.3px;color:#fff}
.contact strong{position:absolute;left:33px;top:9px;font-size:9px;color:#fff;white-space:nowrap}
.contact strong.sm{font-size:4.6px;top:11px}
.follow{left:36px;top:200px;font-family:"Russo One",sans-serif;font-size:8px;color:var(--green)}
.social{top:195px;width:24px;height:24px;border-radius:50%;background:var(--sky)}
</style>
</head>
<body>
<div class="sheet">

  <!-- Cover -->
  <section class="slide cover col-l row1">
    <div class="abs cover-photo" role="img" aria-label="Close-up of a jet engine turbine"></div>
    <div class="abs brand logo">Quelbrion</div>
    <div class="abs welcome">Welcome To</div>
    <div class="abs hero">Quelbrion</div>
    <p class="abs tagline">Unlocking the Future of Airline Operations and the Flying Experience</p>
    <div class="abs site-btn">Website: www.quelbrion.com</div>
  </section>

  <!-- Who We Serve: sectors -->
  <section class="slide col-r row1">
    <div class="band"><h2>Who We Serve</h2></div>
    <div class="abs brand brand-top">Quelbrion</div>
    <div class="abs body" style="left:38px;top:74px;width:182px">
      <p>An innovative approach to weight and balance planning turns estimations into actuals. The Load Insight System unlocks the aircraft's untapped potential, optimizes load planning for more efficient flying and reduced fuel burn. LIS technology provides continuous health monitoring for landing gear systems.</p>
      <p style="margin-top:14px">An optimized center of gravity creates fuel efficiencies which can translate into increased payload and range.</p>
    </div>
    <div class="abs card" style="top:61px">
      <div class="ico"><svg width="18" height="18" viewBox="0 0 24 24" fill="none" stroke="#fff" stroke-width="1.5"><path d="M12 3v18M3 13l9-4 9 4M8 21l4-2 4 2"/></svg></div>
      <h4>COMMERCIAL AVIATION</h4>
      <p>An innovative approach to weight and balance planning turns estimations into actuals.</p>
    </div>
    <div class="abs card" style="top:115px">
      <div class="ico"><svg width="18" height="18" viewBox="0 0 24 24" fill="none" stroke="#fff" stroke-width="1.5"><path d="M4 20L20 4M8 10l-5 1 4 3M14 16l-1 5-3-4"/></svg></div>
      <h4>REGIONAL AND BUSINESS AVIATION</h4>
      <p>Accurate weight and loading data provides actionable information to get the most performance from your aircraft.</p>
    </div>
    <div class="abs card" style="top:169px">
      <div class="ico"><svg width="18" height="18" viewBox="0 0 24 24" fill="none" stroke="#fff" stroke-width="1.5"><path d="M12 2v20M4 15l8-5 8 5M9 21h6"/></svg></div>
      <h4>MILITARY AVIATION</h4>
      <p>Mission ready military aircraft are critical for success – humanitarian or war-fighting initiatives.</p>
    </div>
    <div class="abs foot-green"></div><div class="abs foot-blue"></div>
    <div class="abs brand foot-brand">Quelbrion</div>
    <div class="abs page-no">Page 05 Of 08</div>
    <div class="abs copy">(C) Copyright 2024 | All Rights Reserved</div>
  </section>

  <!-- Table of contents -->
  <section class="slide col-l row2">
    <div class="abs brand brand-top">Quelbrion</div>
    <div class="abs toc-title">Table Of Contents</div>
    <div class="abs toc-sub">(Agenda)</div>
    <p class="abs toc-intro">Sed ut perspiciatis unde omnis iste natus error sit voluptatem accusantium doloremque laudantium, totam rem aperiam, eaque ipsa quae</p>
    <ul class="abs toc-list">
      <li><b>I</b>Introduction</li>
      <li><b>II</b>Table Of Contents (Agenda)</li>
      <li><b>III</b>Who We Are (About Us)</li>
      <li><b>IV</b>Quelbrion Leadership (Team Members)</li>
      <li><b>V</b>Who We Serve</li>
      <li><b>VI</b>Our Sustainability</li>
    </ul>
    <div class="abs foot-green"></div><div class="abs foot-blue"></div>
    <div class="abs brand foot-brand">Quelbrion</div>
    <div class="abs page-no">Page 02 Of 08</div>
    <div class="abs copy">(C) Copyright 2024 | All Rights Reserved</div>
  </section>

  <!-- Quote -->
  <section class="slide quote col-r row2">
    <div class="abs quote-mark">
      <svg width="44" height="44" viewBox="0 0 44 44" fill="#fff"><path d="M13 15h7v8c0 4-2 7-6 8l-1-3c2-1 3-2 3-4h-3zM24 15h7v8c0 4-2 7-6 8l-1-3c2-1 3-2 3-4h-3z"/></svg>
    </div>
    <h3 class="abs">We are dedicated to helping our customers achieve zero carbon emissions by 2050.</h3>
    <p class="abs">Our next-generation technology focuses on improving fuel burn efficiency to significantly reduce CO2 emissions from aircraft, promote sustainability, streamline operations, and contribute to a greener aviation industry.</p>
  </section>

  <!-- About -->
  <section class="slide col-l row3">
    <div class="band"><h2>Who We Are (About Us)</h2></div>
    <div class="abs brand brand-top">Quelbrion</div>
    <div class="abs body" style="left:36px;top:67px;width:182px">
      <p>Quelbrion is an aerospace technology company that produces a game changing onboard weight and balance measurement system - the Load Insight System (LIS). The LIS hardware kit automatically calculates an aircraft's weight and center of gravity for each flight.</p>
      <p style="margin-top:14px">With numerous design, process and method patents, Quelbrion brings a unique combination of engineering innovation and certification expertise within the airline and aerospace industries.</p>
    </div>
    <div class="abs about-photo" role="img" aria-label="Business jet engine and tail at sunset"></div>
    <div class="abs foot-green"></div><div class="abs foot-blue"></div>
    <div class="abs brand foot-brand">Quelbrion</div>
    <div class="abs page-no">Page 03 Of 08</div>
    <div class="abs copy">(C) Copyright 2024 | All Rights Reserved</div>
  </section>

  <!-- Steps -->
  <section class="slide col-r row3">
    <div class="band"><h2>Who We Serve</h2></div>
    <div class="abs brand brand-top">Quelbrion</div>
    <svg class="abs chev" style="left:36px" viewBox="0 0 96 33"><polygon points="6,0 89,0 96,16.5 89,33 0,33 6,16.5" fill="var(--green)"/><g fill="none" stroke="#fff" stroke-width="1"><circle cx="22" cy="12" r="3"/><circle cx="30" cy="12" r="3"/><path d="M17 24c0-4 3-7 5-7s5 3 5 7M25 24c0-4 3-7 5-7s5 3 5 7"/></g></svg>
    <svg class="abs chev" style="left:134px" viewBox="0 0 96 33"><polygon points="6,0 89,0 96,16.5 89,33 0,33 6,16.5" fill="var(--sky)"/><g fill="none" stroke="#fff" stroke-width="1"><circle cx="25" cy="14" r="5"/><path d="M23 20h4v4h-4zM25 4v3M17 8l2 2M33 8l-2 2"/></g></svg>
    <svg class="abs chev" style="left:231px" viewBox="0 0 96 33"><polygon points="6,0 89,0 96,16.5 89,33 0,33 6,16.5" fill="var(--green)"/><g fill="none" stroke="#fff" stroke-width="1"><path d="M20 24l4-8 8-8 3-1-1 3-8 8-8 4z"/><circle cx="29" cy="12" r="1.5"/><path d="M18 20l-3 5M22 22l-3 4"/></g></svg>
    <svg class="abs chev" style="left:328px" viewBox="0 0 96 33"><polygon points="6,0 89,0 96,16.5 89,33 0,33 6,16.5" fill="var(--sky)"/><g fill="none" stroke="#fff" stroke-width="1"><circle cx="25" cy="17" r="9"/><circle cx="25" cy="17" r="5"/><circle cx="25" cy="17" r="1.5"/><path d="M25 17l8-8M31 7v3h3"/></g></svg>
    <div class="abs step" style="left:39px"><h5>STEP 1</h5><p>On the other hand, we denounce with righteous indignation and dislike men who are so beguiled and demoralized by the charms of pleasure of the moment</p></div>
    <div class="abs step" style="left:138px"><h5>STEP 2</h5><p>On the other hand, we denounce with righteous indignation and dislike men who are so beguiled and demoralized by the charms of pleasure of the moment</p></div>
    <div class="abs step" style="left:234px"><h5>STEP 3</h5><p>On the other hand, we denounce with righteous indignation and dislike men who are so beguiled and demoralized by the charms of pleasure of the moment</p></div>
    <div class="abs step" style="left:332px"><h5>STEP 4</h5><p>On the other hand, we denounce with righteous indignation and dislike men who are so beguiled and demoralized by the charms of pleasure of the moment</p></div>
    <div class="abs foot-green"></div><div class="abs foot-blue"></div>
    <div class="abs brand foot-brand">Quelbrion</div>
    <div class="abs page-no">Page 07 Of 08</div>
    <div class="abs copy">(C) Copyright 2024 | All Rights Reserved</div>
  </section>

  <!-- Leadership -->
  <section class="slide col-l row4">
    <div class="band"><h2>Quelbrion Leadership</h2></div>
    <div class="abs brand brand-top">Quelbrion</div>
    <div class="abs leader" style="left:31px">
      <div class="ring"><div class="portrait" role="img" aria-label="Portrait of the founder"></div><span class="badge"></span></div>
      <h4>MARCUS LINDQVIST</h4><p>FOUNDER &amp; SENIOR TECHNICAL FELLOW</p>
    </div>
    <div class="abs leader" style="left:170px">
      <div class="ring"><div class="portrait" role="img" aria-label="Portrait of the CEO"></div><span class="badge"></span></div>
      <h4>DANIEL OKAFOR</h4><p>CEO</p>
    </div>
    <div class="abs leader" style="left:309px">
      <div class="ring"><div class="portrait" role="img" aria-label="Portrait of the chief operating officer"></div><span class="badge"></span></div>
      <h4>PETER HALLWORTH</h4><p>CHIEF OPERATING OFFICER</p>
    </div>
    <div class="abs foot-green"></div><div class="abs foot-blue"></div>
    <div class="abs brand foot-brand">Quelbrion</div>
    <div class="abs page-no">Page 04 Of 08</div>
    <div class="abs copy">(C) Copyright 2024 | All Rights Reserved</div>
  </section>

  <!-- Thank you -->
  <section class="slide thanks col-r row4">
    <div class="abs hex" role="img" aria-label="Jet engine in a maintenance hangar"></div>
    <h2 class="abs">THANK YOU</h2>
    <div class="abs contact" style="top:76px">
      <div class="ico"><svg width="11" height="11" viewBox="0 0 24 24" fill="#fff"><path d="M6 2l4 5-2 3c1 3 3 5 6 6l3-2 5 4-3 4C10 22 2 14 2 5z"/></svg></div>
      <small>CALL US:</small><strong>+1 555 014 2290</strong>
    </div>
    <div class="abs contact" style="top:115px">
      <div class="ico"><svg width="11" height="11" viewBox="0 0 24 24" fill="#fff"><path d="M2 5h20v14H2z"/><path d="M2 5l10 8 10-8" stroke="#3aa" fill="none" stroke-width="1.5"/></svg></div>
      <small>EMAIL US:</small><strong>info@quelbrion.com</strong>
    </div>
    <div class="abs contact" style="top:154px">
      <div class="ico"><svg width="11" height="11" viewBox="0 0 24 24" fill="#fff"><path d="M12 2a7 7 0 0 0-7 7c0 5 7 13 7 13s7-8 7-13a7 7 0 0 0-7-7zm0 10a3 3 0 1 1 0-6 3 3 0 0 1 0 6z"/></svg></div>
      <small>ADDRESS:</small><strong class="sm">4120 Harrow Lane, Suite 300 Austin, Texas 78701</strong>
    </div>
    <div class="abs follow">FOLLOW US:</div>
    <div class="abs social" style="left:92px"></div>
    <div class="abs social" style="left:122px"></div>
  </section>

</div>
</body>
</html>
```